Floor Inspections and Consulting

We provide inspections and consulting services on various floor coverings, e.g. carpet, hardwood, etc. We also do expert witness work for attorneys due to floor covering failures. We current have a logo, just need it incorporated into a new design. I have examples of cards I have found on the internet that capture my attention and make a statement. I have included our original business card, which in my opinion is terrible, but it does have our logo on it.

```html
<!DOCTYPE html>
<html lang="en">
<head>
<meta charset="utf-8">
<title>Groundline – Business Card</title>
<link rel="stylesheet" href="https://fonts.googleapis.com/css2?family=Archivo+Black&family=Roboto:wght@400&display=swap">
<style>
  :root {
    --backdrop: #2a2a2c;
    --card-dark: #1d1d1f;
    --brand-orange: #e8720c;
    --white: #ffffff;
    --rule-grey: #55555a;
  }
  * { box-sizing: border-box; margin: 0; padding: 0; }
  html, body { width: 1200px; height: 1108px; overflow: hidden; }
  body {
    background: var(--backdrop);
    position: relative;
    font-family: "Roboto", Arial, sans-serif;
  }
  .card {
    position: absolute;
    top: 204px;
    width: 400px;
    height: 700px;
    border-radius: 26px;
    overflow: hidden;
  }
  .card--front { left: 160px; background: var(--card-dark); }
  .card--back  { left: 640px; background: var(--brand-orange); }

  /* Front */
  .brand-block {
    position: absolute;
    top: 180px; left: 0; right: 0;
    display: flex; justify-content: center; align-items: center; gap: 12px;
  }
  .brand-block .mark-square { width: 22px; height: 22px; background: var(--brand-orange); }
  .brand-block .name {
    font-family: "Archivo Black", Arial, sans-serif;
    color: var(--brand-orange);
    font-size: 42px;
    line-height: 1;
  }
  .person-name {
    position: absolute;
    top: 392px; left: 0; right: 0;
    text-align: center;
    font-family: "Archivo Black", Arial, sans-serif;
    color: var(--brand-orange);
    font-size: 26px;
    letter-spacing: 0.5px;
  }
  .icon-row {
    position: absolute;
    top: 448px; left: 40px; right: 40px;
    display: flex; align-items: center; gap: 8px;
  }
  .icon-row .rule { flex: 1; height: 1px; background: var(--rule-grey); }
  .icon-row .icon {
    width: 28px; height: 28px;
    background: var(--brand-orange);
    border-radius: 3px;
    display: flex; align-items: center; justify-content: center;
  }
  .contact-list {
    position: absolute;
    top: 494px; left: 0; right: 0;
    list-style: none;
    text-align: center;
    color: var(--white);
    font-size: 21px;
    line-height: 34px;
  }
  .contact-list .accent { color: var(--brand-orange); }

  /* Back */
  .back-brand {
    position: absolute;
    top: 430px; left: 0; right: 0;
    display: flex; justify-content: center; align-items: center; gap: 10px;
  }
  .back-brand .mark-square { width: 18px; height: 18px; background: var(--white); }
  .back-brand .name {
    font-family: "Archivo Black", Arial, sans-serif;
    color: var(--white);
    font-size: 34px;
  }
  .back-tagline {
    position: absolute;
    top: 530px; left: 0; right: 0;
    text-align: center;
    font-family: "Archivo Black", Arial, sans-serif;
    color: var(--white);
    font-size: 23px;
    line-height: 32px;
  }
</style>
</head>
<body>
  <section class="card card--front">
    <div class="brand-block">
      <span class="mark-square"></span>
      <span class="name">GROUNDLINE</span>
    </div>

    <div class="person-name">DANIEL MARLOW</div>

    <div class="icon-row">
      <span class="rule"></span>
      <span class="icon" aria-label="Phone">
        <svg width="16" height="16" viewBox="0 0 24 24"><path fill="#1d1d1f" d="M6.6 10.8a15 15 0 0 0 6.6 6.6l2.2-2.2c.3-.3.7-.4 1-.2 1.1.4 2.3.6 3.6.6.6 0 1 .4 1 1V20c0 .6-.4 1-1 1A17 17 0 0 1 3 4c0-.6.4-1 1-1h3.5c.6 0 1 .4 1 1 0 1.3.2 2.5.6 3.6.1.3 0 .7-.2 1z"/></svg>
      </span>
      <span class="icon" aria-label="Email">
        <svg width="16" height="16" viewBox="0 0 24 24"><rect x="2" y="5" width="20" height="14" fill="none" stroke="#1d1d1f" stroke-width="2"/><path d="M2 5l10 8 10-8" fill="none" stroke="#1d1d1f" stroke-width="2"/></svg>
      </span>
      <span class="icon" aria-label="Website">
        <svg width="16" height="16" viewBox="0 0 24 24"><circle cx="12" cy="12" r="9" fill="none" stroke="#1d1d1f" stroke-width="2"/><path d="M3 12h18M12 3c3 3 3 15 0 18M12 3c-3 3-3 15 0 18" fill="none" stroke="#1d1d1f" stroke-width="1.6"/></svg>
      </span>
      <span class="rule"></span>
    </div>

    <ul class="contact-list">
      <li>555-014-2870</li>
      <li>daniel@groundlinefloors.com</li>
      <li>www.<span class="accent">groundlinefloors</span>.com</li>
    </ul>
  </section>

  <section class="card card--back">
    <div class="back-brand">
      <span class="mark-square"></span>
      <span class="name">GROUNDLINE</span>
    </div>
    <p class="back-tagline">Certified Floor Covering<br>Inspection &amp; Consulting</p>
  </section>
</body>
</html>
```